New Webpage for High Class Expert Witness Services Company

We are looking for a minimalist design for a webpage that just has our logo and an entry form offer to connect with one of our Liaisons.
The entry form should just ask for Name, Email, Contact Info and Description of Project.

Company Name is: The Marlowe Crest Advisory Services

Number of Pages Required

1 page

```html
<!DOCTYPE html>
<html lang="en">
<head>
<meta charset="UTF-8">
<title>The Marlowe Crest Advisory Services – Connect with a Liaison</title>
<link rel="stylesheet" href="https://fonts.googleapis.com/css2?family=Cinzel:wght@600&family=Cormorant+Garamond:wght@700&family=Poppins:wght@400&display=swap">
<style>
  :root {
    --page-bg: #121212;
    --card-bg: #272727;
    --silver: #d8d8d8;
    --silver-dim: #a9a9a9;
    --label: #d0d0d0;
    --field-bg: #e4e4e6;
    --field-text: #8a8a8c;
    --button-ink: #111;
  }
  * { box-sizing: border-box; margin: 0; padding: 0; }
  html, body { width: 1200px; height: 750px; overflow: hidden; }
  body { background: var(--page-bg); position: relative; font-family: "Poppins", sans-serif; }

  .brand {
    position: absolute; left: 344px; top: 61px; width: 512px; height: 84px;
    display: flex; align-items: center; justify-content: center; gap: 18px;
  }
  .brand-mark { width: 40px; height: 40px; background: var(--silver); flex: none; }
  .brand-name {
    font-family: "Cinzel", serif; font-weight: 600; color: var(--silver);
    text-transform: uppercase; line-height: 1.05;
  }
  .brand-name .line-1 { display: block; font-size: 34px; letter-spacing: 1px; }
  .brand-name .line-2 { display: block; font-size: 20px; letter-spacing: 6px; }

  .liaison-card {
    position: absolute; left: 381px; top: 186px; width: 438px; height: 465px;
    background: var(--card-bg);
  }
  .card-title {
    position: absolute; left: 0; top: 36px; width: 100%; text-align: center;
    font-family: "Cormorant Garamond", serif; font-weight: 700; text-transform: uppercase;
    line-height: 21px;
  }
  .card-title .main { display: block; font-size: 19.5px; color: var(--silver); }
  .card-title .sub {
    display: flex; justify-content: center; align-items: center; gap: 7px;
    font-size: 19.5px; color: var(--silver-dim);
  }
  .card-title .sub::before, .card-title .sub::after {
    content: ""; width: 20px; height: 1.5px; background: var(--silver-dim);
  }

  .field-label {
    position: absolute; left: 55px; line-height: 10px;
    font-family: "Cormorant Garamond", serif; font-weight: 700; font-size: 9.5px;
    color: var(--label); text-transform: uppercase; letter-spacing: 0.2px;
  }
  .field {
    position: absolute; left: 38px; width: 361px; height: 43px;
    background: var(--field-bg); padding: 0 16px;
    display: flex; align-items: center;
    font-size: 9px; color: var(--field-text);
  }
  .field.description { height: 72px; align-items: flex-start; padding-top: 14px; }

  .submit {
    position: absolute; left: 38px; top: 393px; width: 361px; height: 43px;
    background: linear-gradient(to bottom, #f2f2f3 0%, #dcdcde 45%, #a9a9ad 100%);
    display: flex; align-items: center; justify-content: center;
    font-family: "Cormorant Garamond", serif; font-weight: 700; font-size: 11.5px;
    color: var(--button-ink); text-transform: uppercase; letter-spacing: 0.3px;
  }
  .submit svg { position: absolute; right: 26px; top: 18px; }
</style>
</head>
<body>
  <header class="brand">
    <span class="brand-mark"></span>
    <div class="brand-name">
      <span class="line-1">The Marlowe Crest</span>
      <span class="line-2">Advisory Services</span>
    </div>
  </header>

  <section class="liaison-card">
    <h1 class="card-title">
      <span class="main">Connect with a Liaison</span>
      <span class="sub">For Your Project</span>
    </h1>

    <div class="field-label" style="top:101px">Your Name*</div>
    <div class="field" style="top:115px">Full name</div>

    <div class="field-label" style="top:169px">Your Email*</div>
    <div class="field" style="top:183px">info@marlowecrest.com</div>

    <div class="field-label" style="top:237px">Contact Info*</div>
    <div class="field" style="top:251px">555-010-2468</div>

    <div class="field description" style="top:307px">Description of Project</div>

    <div class="submit">
      Submit Request
      <svg width="7" height="7" viewBox="0 0 10 10" aria-hidden="true">
        <path d="M10 0 L0 4 L4 5 L5 10 Z" fill="#111"/>
      </svg>
    </div>
  </section>
</body>
</html>
```